New Business Cards for NYC Salon

We are updating all of our cards. 7142-8863-2095 is my account number. We put names of our stylists on their cards. The back should include appointment space. Were looking for something more sleek and modern. Black/White Silver... or even touches of the orange color on our website which has been our thing for years. The design should communicate professional upscale boutique salon for men and women. Should be able to incorporate design into thank you cards, referral cards, brochure and postcards. The file is a zip file...we like the stacked ones black or white or the side versions.

Industry/Entity Type

Beauty Salon

Contact Information for Business Card

Marcus Elling's Salon313 W. 53rd Street, New York NY 10019 212-683-2741 info@marcusellingsalon.example www.marcusellingsalon.example

Font styles to use
Other font styles liked:
• trajan

Requirements
Must have
• we print a different card for every person in the salon. Begin by designing with the name Marcus. We will change it with every employee when printing. Must have a space for appointment date and time.
Nice to have
• Were looking to move towards the stacked or side placed logo but not opposed to utilizing the circular.
Should not have
• Photos

```html
<!DOCTYPE html>
<html lang="en">
<head>
<meta charset="utf-8">
<title>Marcus Elling's Salon — Business Cards</title>
<link rel="stylesheet" href="https://fonts.googleapis.com/css2?family=Cinzel:wght@400&family=Open+Sans:wght@400;600&display=swap">
<style>
  :root {
    --teal: #2dbbb5;
    --charcoal: #2e2e30;
    --paper: #ffffff;
    --ink: #3a3a3c;
    --muted: #5a5a5c;
    --rule: #b8b8ba;
    --backdrop: #ece9e4;
  }
  * { box-sizing: border-box; margin: 0; padding: 0; }
  html, body { width: 1200px; height: 829px; overflow: hidden; }
  body {
    background: var(--backdrop);
    font-family: "Open Sans", Arial, sans-serif;
    position: relative;
  }
  .card {
    position: absolute;
    width: 540px;
    height: 309px;
    background: var(--paper);
    overflow: hidden;
    box-shadow: 0 6px 18px rgba(0,0,0,0.18);
  }
  .card--front { left: 40px; top: 260px; }
  .card--back { left: 620px; top: 260px; }
  .card__art { position: absolute; inset: 0; }

  .wordmark {
    position: absolute;
    display: flex;
    align-items: center;
    gap: 12px;
    font-family: "Cinzel", "Times New Roman", serif;
    color: var(--ink);
    letter-spacing: 0.22em;
    text-transform: uppercase;
    white-space: nowrap;
  }
  .wordmark__square { width: 14px; height: 14px; background: var(--teal); flex: none; }
  .card--front .wordmark { left: 130px; top: 108px; font-size: 20px; }
  .card--back .wordmark { left: 36px; top: 210px; font-size: 13px; gap: 9px; }
  .card--back .wordmark__square { width: 10px; height: 10px; }

  .stylist-name {
    position: absolute;
    right: 22px;
    top: 6px;
    color: var(--paper);
    font-size: 14px;
    font-weight: 400;
  }
  .contact {
    position: absolute;
    left: 290px;
    top: 92px;
    color: var(--muted);
    font-size: 10px;
    line-height: 1.45;
  }
  .contact__salon {
    color: var(--teal);
    font-size: 16px;
    font-weight: 400;
    text-transform: uppercase;
    letter-spacing: 0.02em;
    margin-bottom: 2px;
  }
  .contact__address { margin-bottom: 14px; }
  .contact__phone { margin-bottom: 14px; }

  .appointment {
    position: absolute;
    left: 36px;
    top: 100px;
    width: 220px;
    color: var(--muted);
    font-size: 10px;
  }
  .appointment__title {
    color: var(--teal);
    font-size: 11px;
    font-weight: 600;
    text-transform: uppercase;
    letter-spacing: 0.12em;
    margin-bottom: 10px;
  }
  .appointment__field {
    display: flex;
    align-items: flex-end;
    gap: 8px;
    margin-bottom: 12px;
  }
  .appointment__label { width: 30px; flex: none; }
  .appointment__line { flex: 1; border-bottom: 1px solid var(--rule); height: 12px; }
</style>
</head>
<body>

  <section class="card card--front" aria-label="Card front">
    <svg class="card__art" viewBox="0 0 540 309" aria-hidden="true">
      <rect x="0" y="262" width="540" height="47" fill="var(--charcoal)"/>
      <path d="M190 309 L190 290 Q196 262 230 250 Q250 236 290 232 L440 232 Q470 230 480 210 Q490 190 520 186 L540 186 L540 309 Z" fill="var(--teal)"/>
    </svg>
    <div class="wordmark">
      <span class="wordmark__square"></span>
      <span class="wordmark__name">Marcus Elling's Salon</span>
    </div>
  </section>

  <section class="card card--back" aria-label="Card back">
    <svg class="card__art" viewBox="0 0 540 309" aria-hidden="true">
      <rect x="0" y="0" width="540" height="30" fill="var(--charcoal)"/>
      <path d="M0 0 L296 0 C318 0 318 30 312 46 C306 64 300 80 278 80 L0 80 Z" fill="var(--teal)"/>
      <rect x="0" y="256" width="540" height="8" fill="var(--teal)"/>
      <rect x="0" y="264" width="540" height="45" fill="var(--charcoal)"/>
    </svg>
    <p class="stylist-name">Marcus Elling</p>

    <div class="appointment">
      <p class="appointment__title">Appointment</p>
      <div class="appointment__field"><span class="appointment__label">Date</span><span class="appointment__line"></span></div>
      <div class="appointment__field"><span class="appointment__label">Time</span><span class="appointment__line"></span></div>
    </div>

    <div class="contact">
      <p class="contact__salon">Marcus Elling's Salon</p>
      <p class="contact__address">742 E. 18th Street, New York NY 10003</p>
      <p class="contact__phone">212-683-2741</p>
      <p class="contact__email">info@marcusellingsalon.example</p>
      <p class="contact__web">www.marcusellingsalon.example</p>
    </div>
    <div class="wordmark">
      <span class="wordmark__square"></span>
      <span class="wordmark__name">Marcus Elling's Salon</span>
    </div>
  </section>

</body>
</html>
```